Stylish High End Wedding Videography/Films Website (BMRT)

We need a modern and high-end website look for our wedding video and films business. We films weddings all over the United Kingdom and at European destinations so need something to reflect our work. The website should be visually stunning with images and videos being the focal point as this is what our services are;

I have uploads of some items I like and the features the site needs to have. These have been taken from other websites using standout features.

We need the following pages;

1 - Homepage
2 - Films Index Page
3 - Individual Films Page
4 - Prices / Collection Page
5 - Reviews
6 - Options
7 - About
8 - Contact
9 - Blog Index
10 - Blog Page

All pages must be consistent so have a similar style.

Pages on menu:
Films
Prices
Reviews
Options
About
Contact

We require a responsive look too. Over 90% of our visitors access the website via their mobile devices.

Please use the colours from our logo to incorporate into the website.

Target Market(s)

Wedding Couples

Industry/Entity Type

Wedding Photography

Number of Pages Required

5+ page

Font styles to use
Sans Serif
Script

Requirements
Must have
• The logo must be in the centre of the menu at the top.

Social icons at the bottom of the page.

Use only two fonts including Lore which is supplied
Nice to have
• Different video for each page on the top header. This will play behind the menu.

```html
<!DOCTYPE html>
<html lang="en">
<head>
<meta charset="utf-8">
<title>BMRT – Wedding Films</title>
<link rel="stylesheet" href="https://fonts.googleapis.com/css2?family=Barlow:wght@300;400;500&family=Libre+Baskerville:wght@400;700&display=swap">
<style>
:root{
  --gold:#a08650;
  --gold-light:#c9b27c;
  --ink:#2b2a28;
  --text:#4a4744;
  --beige:#ece7dd;
  --footer:#2e2e2e;
  --footer-line:#5a5855;
  --white:#ffffff;
  --sans:'Barlow',sans-serif;
  --serif:'Libre Baskerville',serif;
}
*{box-sizing:border-box;margin:0;padding:0}
html,body{width:1200px;height:3723px;overflow:hidden;background:var(--white)}
body{position:relative;font-family:var(--serif);color:var(--text)}
.abs{position:absolute}

/* hero */
.hero{left:0;top:0;width:1200px;height:642px;
  background:
    radial-gradient(ellipse 260px 320px at 600px 260px,rgba(214,160,128,.95),rgba(214,160,128,0) 70%),
    radial-gradient(ellipse 300px 380px at 560px 520px,rgba(92,52,34,.9),rgba(92,52,34,0) 70%),
    radial-gradient(ellipse 260px 420px at 260px 380px,rgba(150,96,70,.9),rgba(150,96,70,0) 75%),
    radial-gradient(ellipse 220px 300px at 1100px 360px,rgba(196,96,80,.55),rgba(196,96,80,0) 70%),
    linear-gradient(90deg,#6b4630 0%,#8a5a3e 30%,#7a5438 55%,#5e6a3c 80%,#4c5e32 100%)}
.nav{left:0;top:44px;width:1200px;height:40px}
.nav a{position:absolute;top:0;font-family:var(--sans);font-weight:300;font-size:15px;letter-spacing:.5px;color:var(--white);text-decoration:none;text-transform:uppercase;transform:translateX(-50%)}
.nav a.active{color:var(--gold-light)}
.nav a.active::after{content:"";position:absolute;left:0;right:0;top:22px;height:2px;background:var(--gold-light)}
.brand{left:629px;top:62px;transform:translateX(-50%);font-family:var(--sans);font-weight:500;font-size:15px;letter-spacing:5px;color:var(--white)}
.play{border:1.5px solid rgba(255,255,255,.85);border-radius:50%}
.play::after{content:"";position:absolute;left:50%;top:50%;transform:translate(-35%,-50%);border-left:18px solid var(--white);border-top:11px solid transparent;border-bottom:11px solid transparent}

.intro{left:130px;top:716px;width:940px;text-align:center;font-size:15px;letter-spacing:.5px;line-height:31px;color:var(--text)}

/* film cards */
.film-card{top:885px;width:232px;height:275px;border:3px solid var(--gold)}
.film-card .label{position:absolute;left:8px;right:8px;top:10px;height:45px;background:rgba(255,255,255,.85);text-align:center;font-family:var(--serif)}
.film-card .names{font-size:10px;letter-spacing:4px;padding-top:8px;color:var(--ink)}
.film-card .venue{font-size:8px;letter-spacing:1.5px;margin:5px 14px 0;padding-top:4px;border-top:1px solid var(--ink);color:var(--ink)}
.dots{display:flex;gap:6px}
.dots span{width:11px;height:11px;border-radius:50%;border:1.5px solid var(--ink)}
.dots span.on{background:var(--gold);border-color:var(--gold)}

/* funky section */
.funky{left:0;top:1288px;width:1200px;height:1112px;background:var(--beige)}
.section-title{left:0;width:1200px;text-align:center;font-family:var(--sans);font-weight:500;font-size:33px;color:var(--ink);letter-spacing:.3px}
.section-text{left:135px;width:930px;text-align:center;font-size:15px;letter-spacing:.5px;line-height:31px;color:var(--text)}
.video{border:3px solid var(--gold)}

/* testimonials */
.testimonial{left:163px;top:2639px;width:874px;height:325px;background:var(--white);border-radius:14px;box-shadow:0 2px 14px rgba(0,0,0,.12);overflow:hidden}
.testimonial .backdrop{position:absolute;left:0;top:0;width:430px;height:325px;background:
  radial-gradient(ellipse 140px 180px at 90px 90px,rgba(214,190,170,.7),rgba(214,190,170,0) 70%),
  linear-gradient(90deg,#e8ddd2 0%,#f4efe9 55%,#ffffff 100%)}
.testimonial .avatar{position:absolute;left:184px;top:60px;width:106px;height:106px;border-radius:50%;background:
  radial-gradient(circle at 35% 40%,#e0c6a8,rgba(224,198,168,0) 45%),
  radial-gradient(circle at 70% 45%,#d6b494,rgba(214,180,148,0) 40%),
  linear-gradient(180deg,#dfe6ea 0%,#8a8c90 55%,#2e3a52 100%);border:3px solid var(--white)}
.testimonial .couple{position:absolute;left:80px;width:320px;top:212px;text-align:center;font-family:var(--sans);font-size:22px;color:var(--ink)}
.testimonial .place{position:absolute;left:80px;width:320px;top:250px;text-align:center;font-family:var(--sans);font-weight:300;font-size:15px;letter-spacing:1px;color:var(--text)}
.testimonial .quote-mark{position:absolute;left:400px;top:110px;font-family:var(--serif);font-size:200px;color:#f0eeeb;line-height:1}
.testimonial .quote{position:absolute;left:387px;top:58px;width:448px;font-size:12px;line-height:22px;color:#6b6660;text-align:justify}
.testimonial .quote p.c{text-align:center}

/* footer */
.footer{left:0;top:3116px;width:1200px;height:607px;background:var(--footer);color:var(--white)}
.footer-title{font-family:var(--sans);font-size:28px;color:var(--white)}
.sitemap{left:111px;top:3250px;width:134px;text-align:center}
.sitemap a{display:block;height:34.3px;font-size:16px;color:var(--white);text-decoration:none}
.vrule{width:1px;background:var(--footer-line);top:3204px;height:353px}
.thumb{width:159px;height:157px}
.thumb .play{position:absolute;left:54px;top:53px;width:52px;height:52px}
.thumb .play::after{border-left-width:9px;border-top-width:6px;border-bottom-width:6px}
.contact-info{left:880px;width:285px;text-align:center;font-size:16px;color:var(--white)}
.badge{left:967px;top:3372px;width:110px;height:110px;border-radius:50%;background:#f6eaa0;border:2px solid var(--gold)}
.hrule{left:111px;width:978px;height:1px;background:var(--footer-line)}
.social{left:111px;top:3590px;display:flex;gap:14px}
.social a{font-family:var(--sans);font-size:13px;color:var(--gold);text-decoration:none;letter-spacing:.5px}
.tagline{left:0;width:1200px;text-align:center;font-family:var(--sans);font-size:16px;letter-spacing:.3px;color:var(--white)}
.small{left:0;width:1200px;text-align:center;font-family:var(--sans);font-size:11px;color:#d8d6d2}
</style>
</head>
<body>

<!-- header / hero -->
<div class="abs hero" role="img" aria-label="Laughing bride with groom, warm garden background, video still"></div>
<nav class="abs nav">
  <a class="active" style="left:173px">Home</a>
  <a style="left:275px">Films</a>
  <a style="left:376px">Prices</a>
  <a style="left:487px">Reviews</a>
  <a style="left:778px">Options</a>
  <a style="left:899px">About</a>
  <a style="left:1025px">Contact</a>
</nav>
<div class="abs brand">BMRT</div>
<div class="abs play" style="left:542px;top:263px;width:116px;height:116px"></div>

<p class="abs intro">BMRT is a wedding filmmaker based in the North East of England. We film weddings in a fun and natural way. All weddings are totally unique to the couple. If you are looking for a wedding film for your special day we'd love to hear from you.</p>

<!-- film cards -->
<div class="abs film-card" style="left:111px;background:radial-gradient(ellipse 60px 110px at 70px 200px,#f4f2ee,rgba(244,242,238,0) 80%),linear-gradient(90deg,#8a9a6a 0%,#c8c2b4 35%,#6e6660 60%,#3a3c42 100%)" role="img" aria-label="Bride and groom walking outdoors">
  <div class="label"><div class="names">AMY + DANIEL</div><div class="venue">ASHFORD HALL WEDDING</div></div>
</div>
<div class="abs film-card" style="left:360px;background:radial-gradient(ellipse 110px 130px at 150px 160px,#e8e8e8,rgba(232,232,232,0) 70%),linear-gradient(135deg,#9a9a9a,#3c3c3c)" role="img" aria-label="Black and white close-up of couple">
  <div class="label"><div class="names">LUCY + NOAH</div><div class="venue">MILLBROOK WEDDING</div></div>
</div>
<div class="abs film-card" style="left:609px;background:radial-gradient(ellipse 60px 80px at 150px 240px,#f0ece4,rgba(240,236,228,0) 80%),linear-gradient(180deg,#dfe2e4 0%,#b8aa94 35%,#6e6458 65%,#2e2c2a 100%)" role="img" aria-label="Couple kissing in front of a stone tower in Italy">
  <div class="label"><div class="names">MAYA + KAI</div><div class="venue">ITALY WEDDING</div></div>
</div>
<div class="abs film-card" style="left:857px;background:radial-gradient(ellipse 90px 120px at 160px 140px,#efd8b8,rgba(239,216,184,0) 75%),linear-gradient(90deg,#2f3a52 0%,#6a6a78 40%,#c9a98a 70%,#e9d8b8 100%)" role="img" aria-label="Couple touching foreheads">
  <div class="label"><div class="names">LENA + CONNOR</div><div class="venue">LEICESTERSHIRE WEDDING</div></div>
</div>
<div class="abs dots" style="left:569px;top:1192px"><span class="on"></span><span></span><span></span><span></span></div>

<!-- alternative films -->
<section class="abs funky"></section>
<h2 class="abs section-title" style="top:1366px">PREFER SOMETHING A BIT MORE FUNKY?</h2>
<p class="abs section-text" style="top:1427px">If you are a couple who prefers something a bit different to the styles above then why not go for our alternative option.</p>
<div class="abs video" style="left:114px;top:1517px;width:972px;height:379px;background:radial-gradient(ellipse 240px 200px at 380px 180px,rgba(196,176,150,.8),rgba(196,176,150,0) 70%),radial-gradient(ellipse 200px 160px at 650px 150px,rgba(150,128,104,.7),rgba(150,128,104,0) 70%),linear-gradient(90deg,#3e342a,#6e5e4c 40%,#5a4c3e 70%,#2e2620)" role="img" aria-label="Lace wedding dress hanging on a hanger"></div>
<div class="abs play" style="left:542px;top:1648px;width:116px;height:116px"></div>
<div class="abs video" style="left:114px;top:1935px;width:466px;height:379px;background:radial-gradient(ellipse 110px 110px at 330px 170px,#f2f2f2,rgba(242,242,242,0) 70%),radial-gradient(ellipse 100px 120px at 220px 200px,rgba(40,56,96,.9),rgba(40,56,96,0) 70%),linear-gradient(180deg,#aab4a8 0%,#5e6e42 45%,#3a4a28 100%)" role="img" aria-label="Groom and bride on a rope swing among trees"></div>
<div class="abs play" style="left:289px;top:2066px;width:116px;height:116px"></div>
<div class="abs video" style="left:623px;top:1935px;width:466px;height:379px;background:radial-gradient(ellipse 220px 160px at 230px 150px,#4a4c52,rgba(74,76,82,0) 75%),linear-gradient(135deg,#6a2a30,#2e2e30 40%,#1c1c1e)" role="img" aria-label="Heart-shaped chalk slate sign with hand-lettered message"></div>
<div class="abs play" style="left:798px;top:2066px;width:116px;height:116px"></div>

<!-- testimonials -->
<h2 class="abs section-title" style="top:2478px">TESTIMONIALS</h2>
<p class="abs section-text" style="top:2546px;left:130px;width:940px;font-size:14.5px;letter-spacing:.3px;line-height:24px">I have filmed shot some amazing weddings over the years. My main aim is to ensure that couples enjoy their day and that they take in the moments so they remember them. Our wedding films are almost secondary.</p>
<div class="abs testimonial">
  <div class="backdrop" role="img" aria-label="Faded photo of smiling bride"></div>
  <div class="abs play" style="left:45px;top:138px;width:68px;height:68px;border-color:var(--gold)"></div>
  <div class="avatar" role="img" aria-label="Portrait of the couple"></div>
  <div class="couple">LENA + CONNOR</div>
  <div class="place">KESTREL MANOR, LEICESTERSHIRE</div>
  <div class="quote-mark">“</div>
  <div class="quote">
    <p>One of the best decisions We made was choosing you guys to film our wedding! It's absolutely fantastic, it has everyone so emotional watching it, we can't thank you enough for capturing our special day!</p>
    <p class="c">You were amazing from start to finish</p>
    <p class="c" style="margin-top:22px">Thanks so much.</p>
    <p class="c" style="margin-top:22px">Sarah and Paul<br>Red Lion Ashby</p>
  </div>
</div>
<div class="abs dots" style="left:562px;top:3019px"><span class="on"></span><span></span><span></span><span></span></div>

<!-- footer -->
<footer class="abs footer"></footer>
<div class="abs footer-title" style="left:111px;top:3200px">SITE MAP</div>
<nav class="abs sitemap">
  <a>Blog</a><a>Photos</a><a>Love Stories</a><a>Retro Video</a><a>Moments</a><a>FAQs</a><a>Contact</a>
</nav>
<div class="abs vrule" style="left:331px"></div>
<div class="abs vrule" style="left:868px"></div>

<div class="abs thumb" style="left:429px;top:3204px;background:radial-gradient(ellipse 60px 50px at 50px 40px,#c88a8a,rgba(200,138,138,0) 70%),radial-gradient(ellipse 50px 60px at 120px 110px,#8a6a9a,rgba(138,106,154,0) 70%),linear-gradient(135deg,#5a3a4a,#2a2434)" role="img" aria-label="Guests dancing at reception"><div class="play"></div></div>
<div class="abs thumb" style="left:612px;top:3204px;background:radial-gradient(ellipse 60px 70px at 60px 90px,#b8875e,rgba(184,135,94,0) 70%),linear-gradient(135deg,#efe6da,#c8a47e 70%,#9a7050)" role="img" aria-label="Couple embracing in warm light"><div class="play"></div></div>
<div class="abs thumb" style="left:429px;top:3386px;background:radial-gradient(ellipse 70px 40px at 80px 100px,#e8a090,rgba(232,160,144,0) 70%),radial-gradient(ellipse 60px 60px at 80px 40px,#c08a70,rgba(192,138,112,0) 70%),linear-gradient(135deg,#6a4234,#3a2a24)" role="img" aria-label="Bridesmaid with flower bouquet"><div class="play"></div></div>
<div class="abs thumb" style="left:612px;top:3386px;background:radial-gradient(ellipse 50px 60px at 80px 70px,#f4d0a0,rgba(244,208,160,0) 70%),linear-gradient(90deg,#6a4a30,#c89868 50%,#5a3e28)" role="img" aria-label="Rustic barn ceremony room with lights"><div class="play"></div></div>

<div class="abs footer-title" style="left:948px;top:3200px">CONTACT</div>
<div class="abs contact-info" style="top:3262px">07000 123 456</div>
<div class="abs contact-info" style="top:3305px">hello@bmrtfilms.co.uk</div>
<div class="abs badge" role="img" aria-label="Featured listing badge"></div>

<div class="abs hrule" style="top:3561px"></div>
<nav class="abs social" aria-label="Social links">
  <a>Circle</a><a>Lens</a><a>Reel</a>
</nav>
<div class="abs tagline" style="top:3590px">WEDDING VIDEOGRAPHY - NORTH EAST, UK AND WORLDWIDE FILMS</div>
<div class="abs small" style="top:3628px">BMRT FILMS LIMITED</div>
<div class="abs hrule" style="top:3663px"></div>
<div class="abs small" style="top:3681px;font-size:10px">Copyright © 2020. All rights reserved.</div>

</body>
</html>
```